4th Generation Family Business Needs a New Card Design!

We are a family owned 4th Generation company. We are based in the Sydney, Australia area and we are desperately in need of a more modern and classy card. We are monumental masons who design, supply & erect lasting memorials throughout cemeteries in Sydney. Our customers are normally in a period of grieving. I have attached logo files that will need to be implemented on the card. Company was established 1935. Australian Owned and Operated. Card needs to be designed to PIXO.com specification.

Target Market(s)

Our target market is based upon people that a grieving for family members that have passed away. We also deal with alot of companies that own and operate cemeteries.

Industry/Entity Type

Business

Contact Information for Business Card

Simon Harcourt, Operations Manager, 0417293086, simon@harcourtmemorials.com.au
Lewis Harcourt, Director, 0491630572, lewis@harcourtmemorials.com.au
Phone # 02 9561 3048
Website: www.harcourtmemorials.com.au
Address: Suite 17, 8 Palfrey Lane, West Carlow, Sydney NSW 2156

Font styles to use
Serif
Decorative
Script

Requirements
Must have
• Would like to see the logo nicely implemented with a modern design. Embossed lettering would be a nice additive.

```html
<!DOCTYPE html>
<html lang="en">
<head>
<meta charset="utf-8">
<title>Harcourt Memorials – Business Card</title>
<link rel="stylesheet" href="https://fonts.googleapis.com/css2?family=Cinzel:wght@600&family=Montserrat:wght@600;700&family=Arimo:wght@400&display=swap">
<style>
  :root {
    --backdrop: #e9e6e1;
    --card-white: #ffffff;
    --card-black: #1f1e1e;
    --ink: #1a1a1a;
    --gold: #e8b32a;
    --muted: #3a3a3a;
  }
  * { box-sizing: border-box; margin: 0; padding: 0; }
  html, body { width: 1200px; height: 950px; overflow: hidden; }
  body {
    background: var(--backdrop);
    display: flex;
    align-items: center;
    justify-content: center;
    gap: 70px;
  }
  .card {
    position: relative;
    width: 400px;
    height: 655px;
    border-radius: 4px;
    box-shadow: 0 10px 30px rgba(0,0,0,0.18);
    overflow: hidden;
  }
  .card--front { background: var(--card-white); color: var(--ink); }
  .card--back {
    background: var(--card-black);
    display: flex;
    align-items: center;
    justify-content: center;
  }
  .card__frame { position: absolute; inset: 0; }
  .card__content {
    position: relative;
    height: 100%;
    display: flex;
    flex-direction: column;
    align-items: center;
    padding-top: 86px;
    text-align: center;
  }
  .brand {
    font-family: "Cinzel", serif;
    font-weight: 600;
    line-height: 1.1;
    text-align: center;
    letter-spacing: 1px;
  }
  .card--front .brand { color: var(--ink); font-size: 34px; }
  .card--back .brand { color: #ffffff; font-size: 40px; }
  .person {
    margin-top: 22px;
    display: flex;
    flex-direction: column;
    align-items: center;
  }
  .person__name {
    font-family: "Montserrat", sans-serif;
    font-weight: 700;
    font-size: 22px;
    letter-spacing: 1px;
    text-transform: uppercase;
    margin-top: 4px;
  }
  .person__role {
    font-family: "Montserrat", sans-serif;
    font-weight: 600;
    font-size: 15px;
    letter-spacing: 1px;
    color: var(--gold);
    text-transform: uppercase;
  }
  .contact {
    list-style: none;
    margin-top: 10px;
    font-family: "Arimo", sans-serif;
    font-size: 15px;
    color: var(--muted);
    line-height: 1.35;
  }
  .contact__item {
    display: flex;
    flex-direction: column;
    align-items: center;
    margin-top: 8px;
  }
  .icon { width: 16px; height: 16px; fill: var(--ink); margin-bottom: 3px; }
</style>
</head>
<body>

  <article class="card card--front">
    <svg class="card__frame" viewBox="0 0 400 655" aria-hidden="true">
      <path d="M40 20 H360 V40 H380 V615 H360 V635 H40 V615 H20 V40 H40 Z"
            fill="none" stroke="#1a1a1a" stroke-width="6"/>
      <path d="M48 30 H352 V48 H370 V607 H352 V625 H48 V607 H30 V48 H48 Z"
            fill="none" stroke="#1a1a1a" stroke-width="1.5"/>
    </svg>
    <div class="card__content">
      <p class="brand">Harcourt<br>Memorials</p>

      <div class="person">
        <svg class="icon" viewBox="0 0 16 16" aria-hidden="true">
          <circle cx="8" cy="5" r="3.5"/><path d="M1.5 16 C1.5 10 14.5 10 14.5 16 Z"/>
        </svg>
        <h1 class="person__name">Simon Harcourt</h1>
        <p class="person__role">Operations Manager</p>
      </div>

      <ul class="contact">
        <li class="contact__item">
          <svg class="icon" viewBox="0 0 16 16" aria-hidden="true">
            <path d="M8 0 C4.5 0 2.5 2.5 2.5 5.5 C2.5 9.5 8 16 8 16 C8 16 13.5 9.5 13.5 5.5 C13.5 2.5 11.5 0 8 0 Z M8 3.5 A2 2 0 1 1 8 7.5 A2 2 0 1 1 8 3.5 Z"/>
          </svg>
          <span>Suite 17, 8 Palfrey Lane<br>West Carlow, Sydney NSW 2156</span>
        </li>
        <li class="contact__item">
          <svg class="icon" viewBox="0 0 16 16" aria-hidden="true">
            <path d="M1 5 C1 2 15 2 15 5 V7 H11 V5.5 H5 V7 H1 Z"/><rect x="3" y="8" width="10" height="7" rx="1"/>
          </svg>
          <span>02 9561 3048</span>
        </li>
        <li class="contact__item">
          <svg class="icon" viewBox="0 0 16 16" aria-hidden="true">
            <rect x="4" y="0.5" width="8" height="15" rx="1.5"/><rect x="5.5" y="2.5" width="5" height="9" fill="#fff"/>
          </svg>
          <span>0417293086</span>
        </li>
        <li class="contact__item">
          <svg class="icon" viewBox="0 0 16 16" aria-hidden="true">
            <rect x="0.5" y="3" width="15" height="10" rx="1"/><path d="M1 4 L8 9 L15 4" fill="none" stroke="#fff" stroke-width="1.2"/>
          </svg>
          <span>simon@harcourtmemorials.com.au</span>
        </li>
        <li class="contact__item">
          <svg class="icon" viewBox="0 0 16 16" aria-hidden="true">
            <circle cx="8" cy="8" r="7.5"/><path d="M0.5 8 H15.5 M8 0.5 C4 5 4 11 8 15.5 M8 0.5 C12 5 12 11 8 15.5" fill="none" stroke="#fff" stroke-width="1"/>
          </svg>
          <span>www.harcourtmemorials.com.au</span>
        </li>
      </ul>
    </div>
  </article>

  <article class="card card--back">
    <p class="brand">Harcourt<br>Memorials</p>
  </article>

</body>
</html>
```